Request for Business Card Design

Hi. My name is Marlene, I am looking for a new business card design for my company, Quarrow Signal Instruments, LLC. I really like the design you did for Tarsel Venture and was hoping you could do something similar using our full logo and our mark. I am also open to any raised texture design using our mark. I have attached our full logo, which would need to be somewhere on the card, as well as the mark in both outline and full form, as well as our brand colors / guide. The card does not have to be white, as long as our logo and mark appear. I actually like darker colored business cards more, but am open to all options. If you are interested in working with me, please let me know. We would also take the business card design into letterhead design if you can do that.

```html
<!DOCTYPE html>
<html lang="en">
<head>
<meta charset="utf-8">
<title>Quarrow Signal Instruments – Business Card</title>
<link rel="stylesheet" href="https://fonts.googleapis.com/css2?family=Barlow:wght@400;500;600&family=Montserrat:wght@500;700&display=swap">
<style>
  :root {
    --stage-light: #ececec;
    --stage-dark: #8a8a8a;
    --card-dark: #3c3c3e;
    --card-deep: #242123;
    --card-soft: #58565a;
    --accent-blue: #2a93bf;
    --shadow-line: #1c1a1c;
    --ink-light: #f4f4f4;
  }
  * { box-sizing: border-box; margin: 0; padding: 0; }
  html, body { width: 1200px; height: 1200px; overflow: hidden; }
  body {
    background: linear-gradient(120deg, var(--stage-light) 0%, #c4c4c4 55%, var(--stage-dark) 100%);
    position: relative;
    font-family: "Barlow", sans-serif;
  }
  .card {
    position: absolute;
    left: 220px;
    width: 760px;
    height: 434px;
    border-radius: 26px;
    overflow: hidden;
    box-shadow: 0 6px 0 #111, 0 18px 30px rgba(0,0,0,0.25);
  }
  .card-front {
    top: 110px;
    background: linear-gradient(115deg, #6a6a6d 0%, #4b4b4e 45%, var(--card-dark) 100%);
    display: flex;
    align-items: center;
    justify-content: center;
  }
  .brand {
    display: flex;
    align-items: center;
    gap: 26px;
    color: var(--ink-light);
  }
  .brand-dot {
    border-radius: 50%;
    background: var(--ink-light);
    flex: none;
  }
  .brand-name {
    font-family: "Barlow", sans-serif;
    font-weight: 600;
    letter-spacing: 0.06em;
    text-transform: uppercase;
    line-height: 1.1;
  }
  .card-front .brand-dot { width: 92px; height: 92px; }
  .card-front .brand-name { font-size: 42px; }

  .card-back { top: 640px; background: var(--card-dark); }
  .back-shapes { position: absolute; inset: 0; width: 760px; height: 434px; }
  .back-brand {
    position: absolute;
    left: 54px;
    top: 182px;
    gap: 16px;
  }
  .back-brand .brand-dot { width: 52px; height: 52px; }
  .back-brand .brand-name { font-size: 21px; }

  .contact {
    position: absolute;
    right: 40px;
    top: 40px;
    width: 380px;
    text-align: right;
    color: var(--ink-light);
  }
  .contact-name {
    font-family: "Montserrat", sans-serif;
    font-weight: 700;
    font-size: 34px;
    color: var(--accent-blue);
    letter-spacing: 0.02em;
  }
  .contact-role {
    font-family: "Montserrat", sans-serif;
    font-weight: 500;
    font-size: 18px;
    margin-top: 4px;
    letter-spacing: 0.03em;
  }
  .contact-rule {
    height: 3px;
    width: 290px;
    background: var(--accent-blue);
    margin: 14px 0 0 auto;
  }
  .contact-address {
    margin-top: 34px;
    font-size: 19px;
    line-height: 1.3;
    letter-spacing: 0.04em;
  }
  .contact-list { list-style: none; margin-top: 16px; }
  .contact-list li {
    display: flex;
    justify-content: flex-end;
    align-items: center;
    gap: 10px;
    font-size: 19px;
    line-height: 1.45;
    letter-spacing: 0.04em;
  }
  .contact-icon { width: 16px; height: 16px; fill: var(--accent-blue); flex: none; }
</style>
</head>
<body>

  <section class="card card-front" aria-label="Business card front">
    <div class="brand">
      <span class="brand-dot"></span>
      <span class="brand-name">Quarrow Signal<br>Instruments</span>
    </div>
  </section>

  <section class="card card-back" aria-label="Business card back">
    <svg class="back-shapes" viewBox="0 0 760 434" aria-hidden="true">
      <defs>
        <linearGradient id="panelShade" x1="0" y1="0" x2="1" y2="1">
          <stop offset="0" stop-color="#58565a"/>
          <stop offset="1" stop-color="#242123"/>
        </linearGradient>
      </defs>
      <path d="M0,0 H310 C318,170 488,230 494,434 H0 Z" fill="#2a93bf"/>
      <path d="M0,0 H292 C300,170 470,235 476,434 H0 Z" fill="#1c1a1c"/>
      <path d="M0,0 H284 C292,172 462,238 468,434 H0 Z" fill="url(#panelShade)"/>
    </svg>

    <div class="brand back-brand">
      <span class="brand-dot"></span>
      <span class="brand-name">Quarrow Signal<br>Instruments</span>
    </div>

    <div class="contact">
      <h1 class="contact-name">Marlene</h1>
      <p class="contact-role">Founder &amp; Director</p>
      <div class="contact-rule"></div>
      <p class="contact-address">1180 Harlow Ridge Road.<br>Bellmont, CO 80611</p>
      <ul class="contact-list">
        <li>+001 555 210 4837
          <svg class="contact-icon" viewBox="0 0 16 16" aria-label="Phone"><path d="M3.5 1.5l2.5 3-1.5 1.5c.8 2 2.5 3.7 4.5 4.5L10.5 9l3 2.5-1.5 2.5C6.5 14 2 9.5 1 4z"/></svg>
        </li>
        <li>+001 555 210 4890
          <svg class="contact-icon" viewBox="0 0 16 16" aria-label="Fax"><path d="M4 1h8v4H4z M1 6h14v6h-2v-2H3v2H1z M4 11h8v4H4z"/></svg>
        </li>
        <li>info@quarrowsignal.com
          <svg class="contact-icon" viewBox="0 0 16 16" aria-label="Email"><path d="M1 3h14v1L8 9 1 4z M1 6l7 5 7-5v7H1z"/></svg>
        </li>
        <li>www.quarrowsignal.com
          <svg class="contact-icon" viewBox="0 0 16 16" aria-label="Website"><circle cx="8" cy="8" r="7"/><path d="M1 8h14M8 1c-3 3.5-3 10.5 0 14M8 1c3 3.5 3 10.5 0 14" stroke="#3c3c3e" stroke-width="1.2" fill="none"/></svg>
        </li>
      </ul>
    </div>
  </section>

</body>
</html>
```